Mandala Postcard Design

I am in need of a postcard to hand out at a Psychic Fair. I envision the card to having half-of-a Mandala (from my Facebook folder), touched up a bit to make it vibrant and bold. Others vendors will have cards w/photographic backgrounds doing yoga. I'd like mine to stand out for it's line-drawn "cartoonish" nature, solid-color nature. The wording would be my basic contact info and a short description ... something like: "Experience the Magic of Mandala Making ... Next Class will be held: (open space for writing, no lines) The art is contained in this Facebook folder. Lots to choose from, with my favorites being the stronger outlined designs.

https://www.examplesocial.net/Brightorbs/media_set?set=a.20462926615637197.2184852941.783542196&type=3
Updates

I just uploaded a few new drawings that might work better, since they are more round. I want to minimize the white space, for instance, avoid having the left & right corners empty. Another idea could be to use 1/4 mandalas in the corners. I'm ready to make a decision. I want it to look great, but as I gain drawing experience, I'll need to update my cards. Thanks! I'm not sure if this the place for this comment, but I'll also be needing a DVD label for my tutorials, and a front page design for a mandala coloring book.

Target Market(s)

Primarily women interested in metaphysical, psychic, meditation, reiki and a basic interest in art.

Font styles to use
Serif
Sans Serif

Requirements
Should not have
• Should not be on a dark card, really should be a plain white background, it seems, in order to stand out.

```html
<!DOCTYPE html>
<html lang="en">
<head>
<meta charset="utf-8">
<title>Experience the Magic of Mandala Making</title>
<link rel="stylesheet" href="https://fonts.googleapis.com/css2?family=Fredericka+the+Great&family=Josefin+Sans:wght@300&family=Roboto:wght@400&display=swap">
<style>
  :root {
    --paper: #ffffff;
    --ink: #111111;
    --navy: #1d1f4f;
    --magenta: #e0367a;
    --red: #e2262f;
    --teal: #2bb9b3;
    --yellow: #f3d21c;
    --pink: #f49ab8;
    --sky: #4aa3e0;
  }
  html, body {
    margin: 0;
    padding: 0;
    overflow: hidden;
    background: var(--paper);
  }
  .postcard {
    position: relative;
    width: 1200px;
    height: 929px;
    background: var(--paper);
    overflow: hidden;
  }
  .mandala {
    position: absolute;
    border-radius: 50%;
  }
  .mandala--top-left {
    left: -110px; top: -120px;
    width: 330px; height: 300px;
    background: radial-gradient(circle at 45% 45%, var(--yellow) 0 12%, var(--magenta) 13% 32%, var(--teal) 33% 52%, var(--navy) 53% 60%, rgba(255,255,255,0) 61%);
  }
  .mandala--top-right {
    left: 880px; top: -110px;
    width: 340px; height: 340px;
    background: radial-gradient(circle, var(--yellow) 0 10%, var(--navy) 11% 30%, var(--magenta) 31% 48%, var(--teal) 49% 60%, var(--navy) 61% 66%, var(--pink) 67% 70%, rgba(255,255,255,0) 71%);
  }
  .mandala--centre-left {
    left: 20px; top: 200px;
    width: 410px; height: 410px;
    background: radial-gradient(circle, var(--yellow) 0 6%, var(--navy) 7% 18%, var(--magenta) 19% 30%, var(--sky) 31% 42%, var(--navy) 43% 56%, var(--teal) 57% 62%, var(--red) 63% 66%, rgba(255,255,255,0) 67%);
  }
  .mandala--bottom-left {
    left: -40px; top: 690px;
    width: 290px; height: 290px;
    background: radial-gradient(circle, var(--yellow) 0 10%, var(--magenta) 11% 28%, var(--teal) 29% 44%, var(--navy) 45% 52%, var(--pink) 53% 60%, rgba(255,255,255,0) 61%);
  }
  .mandala--bottom-right {
    left: 720px; top: 590px;
    width: 620px; height: 620px;
    background: radial-gradient(circle, var(--yellow) 0 8%, var(--navy) 9% 20%, var(--sky) 21% 30%, var(--pink) 31% 44%, var(--magenta) 45% 52%, var(--teal) 53% 58%, var(--navy) 59% 64%, rgba(255,255,255,0) 65%);
  }
  .headline {
    position: absolute;
    left: 520px;
    top: 270px;
    width: 660px;
    margin: 0;
    text-align: center;
    font-family: "Josefin Sans", sans-serif;
    font-weight: 300;
    font-size: 42px;
    line-height: 84px;
    letter-spacing: 2px;
    color: var(--ink);
  }
  .headline__initial {
    font-family: "Fredericka the Great", serif;
    font-size: 64px;
  }
  .next-class {
    position: absolute;
    left: 634px;
    top: 468px;
    margin: 0;
    font-family: "Roboto", sans-serif;
    font-size: 20px;
    color: var(--ink);
  }
</style>
</head>
<body>
  <main class="postcard">
    <div class="mandala mandala--top-left" role="img" aria-label="Quarter mandala drawing in yellow, magenta, teal and navy"></div>
    <div class="mandala mandala--top-right" role="img" aria-label="Partial mandala drawing in navy, magenta and teal"></div>
    <div class="mandala mandala--centre-left" role="img" aria-label="Full mandala drawing in navy, magenta, blue and teal with red petals"></div>
    <div class="mandala mandala--bottom-left" role="img" aria-label="Quarter mandala drawing in magenta, teal and navy"></div>
    <div class="mandala mandala--bottom-right" role="img" aria-label="Large partial mandala drawing in pink, blue, teal and navy"></div>

    <h1 class="headline">
      <span class="headline__initial">E</span>xperience the <span class="headline__initial">M</span>agic of<br>
      <span class="headline__initial">M</span>andala <span class="headline__initial">M</span>aking
    </h1>
    <p class="next-class">Next Class will be held :</p>
  </main>
</body>
</html>
```